Events publishing website

Have increased the budget for Coded website design. Thanks
-
We need a wordpress website for events publishing. The website will be using all different kinds of events (social, business, music etc). The website should allow user to submit the new events. the new events will be published after admin reviewed.
Key menu items & requirements
- New Events (1-show picture, short description & start/end date. User can view more details in another page. 2-have categories, such as locations, free/ticked, event type etc. 3 - allow user to share the events in social website)
- Event organizer list (show the full list and most popular event organizers. users can view the list by categories, similar to above)
- events establishments (allow user to publish events related informations such as equipments, venue informations etc)
- discussion forum
Key functions
-registration page (new users should fill name, location, normal users or event organizer, types of event organizer etc)
-allow user to change locations to view different events
-search function
The functions should be similar to the following, the design should not. The website should not look like a proper website.
http://www.plavorgatherings.example
Reason: Hi All, have extended few days to allow some changes to be made for current design. Thanks

```html
<!DOCTYPE html>
<html lang="en">
<head>
<meta charset="utf-8">
<title>Events – Registration</title>
<link rel="stylesheet" href="https://fonts.googleapis.com/css2?family=Signika:wght@300;400&family=Open+Sans:wght@400;600&display=swap">
<style>
:root{
  --page:#efece5;
  --ink:#222;
  --teal:#4f857d;
  --teal-dark:#3b6d66;
  --teal-deep:#2f5d57;
  --orange:#f0a521;
  --line:#d9d9d9;
  --label:#333;
  --white:#fff;
}
*{box-sizing:border-box;margin:0;padding:0}
html,body{width:773px;height:1200px;overflow:hidden}
body{position:relative;background:var(--page);font-family:"Open Sans",sans-serif;color:var(--ink)}
.topbar{position:absolute;left:0;top:0;width:773px;height:22px;background:#111;color:#fff;font-size:8px;display:flex;align-items:center;padding-left:22px;letter-spacing:.2px;white-space:nowrap}
.topbar .sep{margin:0 8px}
.brand{position:absolute;left:29px;top:46px;font-family:"Signika",sans-serif}
.brand-name{font-size:29px;font-weight:300;color:var(--teal-dark);line-height:1}
.brand-slogan{font-size:12px;font-weight:300;color:var(--teal-dark);margin-top:1px}
.account{position:absolute;top:36px;left:548px;display:flex;gap:15px;font-family:"Signika",sans-serif;font-weight:300;font-size:11px;color:var(--teal-deep);text-transform:uppercase;white-space:nowrap}
.account a{display:flex;align-items:flex-end;gap:3px;text-decoration:none;color:inherit}
.search{position:absolute;left:537px;top:71px;width:220px;height:25px;display:flex}
.search-field{flex:1;border:1px solid #ddd;border-right:0;background:#fff;border-radius:3px 0 0 3px;font-size:9.5px;color:#888;padding:0 8px;display:flex;align-items:center;font-family:"Signika",sans-serif;font-weight:300}
.search-go{width:25px;background:var(--orange);color:#fff;border-radius:0 3px 3px 0;font-size:11px;display:flex;align-items:center;justify-content:center;font-family:"Signika",sans-serif}
.mainnav{position:absolute;left:22px;top:110px;width:738px;height:43px;background:var(--teal);display:flex;border-bottom:2px solid #fff}
.mainnav a{font-family:"Signika",sans-serif;font-weight:300;color:#fff;text-decoration:none;font-size:13.5px;display:flex;align-items:center;justify-content:center;border-right:1px dashed #2f5d57;text-transform:uppercase;white-space:nowrap;flex:none}
.mainnav a:last-child{border-right:0}
.hero{position:absolute;left:22px;top:154px;width:738px;height:229px;background:linear-gradient(90deg,#3d4d52 0%,#6b5a4d 35%,#4a2a1e 55%,#c9651f 72%,#e9a02a 82%,#8a3b1c 100%)}
.hero-arrow{position:absolute;top:243px;width:20px;height:32px;background:#f4f1ea;display:flex;align-items:center;justify-content:center;color:#777;font-size:14px}
.hero-arrow.prev{left:22px;border-radius:0 16px 16px 0}
.hero-arrow.next{left:740px;border-radius:16px 0 0 16px}
.panel{position:absolute;left:29px;top:389px;width:724px;height:566px;background:#fff;border:1px solid #ddd}
.panel-title{position:absolute;left:23px;top:30px;font-family:"Signika",sans-serif;font-weight:400;font-size:13px;color:#222;padding-bottom:8px;border-bottom:1px dotted #777;width:134px}
.field{position:absolute;left:0;width:724px;height:26px}
.field label{position:absolute;right:492px;top:5px;font-size:12px;font-weight:300;color:var(--label);font-family:"Signika",sans-serif;white-space:nowrap;text-align:right}
.input{position:absolute;left:250px;top:0;width:193px;height:26px;border:1px solid var(--line);border-radius:3px;background:linear-gradient(#fafafa,#fff)}
.input.select::after{content:"";position:absolute;right:9px;top:9px;width:4px;height:4px;border-right:1px solid #555;border-bottom:1px solid #555;transform:rotate(45deg)}
.input.area{height:79px}
.submit{position:absolute;left:362px;top:497px;width:80px;height:27px;background:var(--teal-deep);color:#fff;border-radius:3px;font-family:"Signika",sans-serif;font-weight:300;font-size:12px;display:flex;align-items:center;justify-content:center}
.footer{position:absolute;left:22px;top:970px;width:738px;height:230px;background:linear-gradient(#5a8f87,#3f716a)}
.footer h3{position:absolute;font-family:"Signika",sans-serif;font-weight:300;font-size:14px;color:#fff}
.quicklinks{position:absolute;left:32px;top:40px;width:418px}
.quicklinks .row{display:flex;height:21px;align-items:center;border-bottom:1px dashed #8db3ad;font-size:9px;color:#fff;white-space:nowrap}
.quicklinks .row span:nth-child(1){width:83px;padding-left:3px}
.quicklinks .row span:nth-child(2){width:106px}
.quicklinks .row span:nth-child(3){width:105px}
.social{position:absolute;left:494px;top:40px;display:flex;gap:4px}
.social span{width:20px;height:20px;border-radius:50%;background:#e8efee}
.copyright{position:absolute;left:16px;top:158px;width:707px;height:35px;background:rgba(40,80,74,.55);border-radius:2px;font-size:7.5px;color:#e8f0ee;display:flex;align-items:center;padding-left:14px;white-space:nowrap}
</style>
</head>
<body>
<nav class="topbar">EVENTS<span class="sep">|</span>NEWS EVENTS<span class="sep">|</span>RELISH<span class="sep">|</span>EVENT INTERNATIONAL ART SERIES<span class="sep">|</span>PLAVOR EVENTS CALENDAR</nav>

<header>
  <div class="brand">
    <div class="brand-name">Events</div>
    <div class="brand-slogan">your company slogan here</div>
  </div>
  <div class="account">
    <a href="#"><svg width="14" height="14" viewBox="0 0 14 14"><rect x="0" y="6" width="3" height="8" fill="#2f5d57"/><path d="M4 6 L7 1 Q9 1 8.5 4 L8 6 H13 Q14 7 13 8 L12 13 H4 Z" fill="#2f5d57"/></svg>Sign up</a>
    <a href="#"><svg width="12" height="15" viewBox="0 0 12 15"><path d="M3 7V4a3 3 0 0 1 6 0v3" stroke="#2f5d57" stroke-width="2" fill="none"/><rect x="0" y="7" width="12" height="8" rx="1" fill="#2f5d57"/></svg>Login</a>
    <a href="#"><svg width="16" height="16" viewBox="0 0 16 16"><circle cx="8" cy="4.5" r="4" fill="#2f5d57"/><path d="M0 16 Q1 9 8 9 Q15 9 16 16 Z" fill="#2f5d57"/></svg>Member</a>
  </div>
  <div class="search"><div class="search-field">Enter Keyword here</div><div class="search-go">Go</div></div>
</header>

<nav class="mainnav">
  <a href="#" style="width:74px">Main</a><a href="#" style="width:86px">Popular</a><a href="#" style="width:78px">Events</a><a href="#" style="width:67px">Help</a><a href="#" style="width:89px">Support</a><a href="#" style="width:81px">Contact</a><a href="#" style="width:138px">Event Organizer</a><a href="#" style="width:125px;justify-content:flex-start;padding-left:19px">Forum</a>
</nav>

<div class="hero" role="img" aria-label="Conference hall with rows of chairs, projection screens and stage lit in red and amber"></div>
<div class="hero-arrow prev">&#10094;</div>
<div class="hero-arrow next">&#10095;</div>

<main class="panel">
  <h2 class="panel-title">Registration</h2>
  <div class="field" style="top:83px"><label>First Name :</label><div class="input"></div></div>
  <div class="field" style="top:129px"><label>Last Name :</label><div class="input"></div></div>
  <div class="field" style="top:175px"><label>Email :</label><div class="input"></div></div>
  <div class="field" style="top:220px"><label>Show the Venue :</label><div class="input select"></div></div>
  <div class="field" style="top:266px"><label>Date :</label><div class="input select"></div></div>
  <div class="field" style="top:312px"><label>Performance :</label><div class="input select"></div></div>
  <div class="field" style="top:358px"><label>Speaker :</label><div class="input"></div></div>
  <div class="field" style="top:404px"><label>Comments :</label><div class="input area"></div></div>
  <div class="submit">SUBMIT</div>
</main>

<footer class="footer">
  <h3 style="left:32px;top:13px">Quick Links</h3>
  <div class="quicklinks">
    <div class="row"><span>Hom page</span><span>Login</span><span>Support</span><span>Term &amp; Conditions of Use</span></div>
    <div class="row"><span>Events</span><span>FAQ</span><span>Add Events</span><span>Privacy Policy</span></div>
    <div class="row"><span>Popular</span><span>Login</span><span>Speical Events</span><span>Help</span></div>
    <div class="row"><span>News</span><span>Forgot Password</span><span>Contact info</span><span></span></div>
  </div>
  <h3 style="left:493px;top:13px">Connect with Us</h3>
  <div class="social"><span></span><span></span><span></span></div>
  <div class="copyright">© 2012 Company Name &nbsp;|&nbsp; All right reserved &nbsp;|&nbsp; Policy Privacy</div>
</footer>
</body>
</html>
```